Stylish new business card needed!

Hello everyone! I am in need of a new business card design for an alarm company here in Hurricane WV. I have all fonts, color codes and logos provided for you use! We are a young company and like the style of a clean sleek looking business card. Would like it double sided, one side holding the logo and the other with your design!
Target Market(s)
The people that are looking for the newest tech for home automation and security
Industry/Entity Type
Alarm services; Home automation
Contact Information for Business Card
Name of person; position (Sales; Installer); Phone Number (555.418.7260); Employee cell Number; Website (www.GuardedByVelk.example); Employee Email; Double sided
Look and feel
Each slider illustrates characteristics of the customer's brand and the style your logo design should communicate.

```html
<!DOCTYPE html>
<html lang="en">
<head>
<meta charset="utf-8">
<title>Velk Business Card</title>
<link href="https://fonts.googleapis.com/css2?family=Archivo+Black&family=Lato:wght@400;700&display=swap" rel="stylesheet">
<style>
  :root{
    --backdrop:#2e2e2e;
    --card:#1d1e1e;
    --emboss:#262727;
    --grey:#9a9a9a;
    --orange:#f58a3f;
    --white:#f4f4f4;
  }
  *{margin:0;padding:0;box-sizing:border-box}
  html,body{width:1200px;height:937px;overflow:hidden;background:var(--backdrop)}
  .canvas{position:relative;width:1200px;height:937px;display:flex;flex-direction:column;align-items:center;justify-content:center;gap:44px}
  .card{position:relative;width:700px;height:400px;background:var(--card);box-shadow:0 8px 22px rgba(0,0,0,.45)}
  .brand{display:flex;align-items:center;gap:18px;font-family:"Lato",sans-serif;font-weight:700;letter-spacing:2px}
  .card-front .brand{position:absolute;left:50%;top:50%;transform:translate(-50%,-50%)}
  .card-front .brand-name{font-size:110px;color:var(--emboss)}
  .card-front .brand-dot{width:46px;height:46px;border-radius:50%;background:var(--emboss)}
  .card-back .brand{position:absolute;left:70px;top:120px}
  .card-back .brand-name{font-size:92px;color:var(--grey)}
  .card-back .brand-dot{width:38px;height:38px;border-radius:50%;background:var(--orange)}
  .contact{position:absolute;left:420px;top:118px;font-family:"Lato",sans-serif;color:var(--white)}
  .contact-name{font-family:"Archivo Black",sans-serif;font-size:30px;color:var(--orange);letter-spacing:.5px;line-height:1}
  .contact-role{font-size:17px;margin-top:4px}
  .contact-list{list-style:none;margin-top:22px;font-size:17px;line-height:1.55}
  .contact-list li{display:flex;align-items:center;gap:10px}
  .contact-list li.plain{padding-left:24px}
  .icon{width:14px;height:14px;fill:var(--orange);flex:none}
</style>
</head>
<body>
<main class="canvas">
  <section class="card card-front" aria-label="Card front">
    <div class="brand"><span class="brand-dot"></span><span class="brand-name">Velk</span></div>
  </section>

  <section class="card card-back" aria-label="Card back">
    <div class="brand"><span class="brand-dot"></span><span class="brand-name">Velk</span></div>
    <div class="contact">
      <p class="contact-name">DANA WHITLOCK</p>
      <p class="contact-role">Manager</p>
      <ul class="contact-list">
        <li>
          <svg class="icon" viewBox="0 0 14 14"><path d="M3 0h8a1 1 0 0 1 1 1v12a1 1 0 0 1-1 1H3a1 1 0 0 1-1-1V1a1 1 0 0 1 1-1zm0 2v9h8V2zm4 9.6a.8.8 0 1 0 0 1.6.8.8 0 0 0 0-1.6z"/></svg>
          000-000-0000
        </li>
        <li>
          <svg class="icon" viewBox="0 0 14 14"><path d="M3 1l2.4 2.6-1.3 1.6a8 8 0 0 0 4.7 4.7l1.6-1.3L13 11l-1.3 2C6 13 1 8 1 2.3z"/></svg>
          555.418.7260
        </li>
        <li>
          <svg class="icon" viewBox="0 0 14 14"><path d="M0 3h14v1.2L7 8.4 0 4.2zm0 2.6l7 4.2 7-4.2V11H0z"/></svg>
          mail@GuardedByVelk.example
        </li>
        <li>
          <svg class="icon" viewBox="0 0 14 14"><circle cx="7" cy="7" r="6.5"/><path d="M.5 7h13M7 .5c3 3.5 3 9.5 0 13M7 .5c-3 3.5-3 9.5 0 13" stroke="#1d1e1e" stroke-width="1" fill="none"/></svg>
          www.GuardedByVelk.example
        </li>
      </ul>
    </div>
  </section>
</main>
</body>
</html>
```